Quillmarsh Property Solutions need a business card design

Hello guys. We would need a business card design asap please.
We are a start up property investment business based in London UK specialised in buying, selling, managing and letting properties and helping distressed property owners.
The name of our Business is Quillmarsh, the logo symbolises the four fundamental elements of the world (earth, air, fire and water) and so it stands for strength, stability, longevity.
We would like the business card to communicate professionalism and reliability. Many many thanks indeed for your work.

Details:

1.) Rosalind Updike
Property Investor
Mobile: +44(0)7700123456
Email: rosalind.quillmarsh@mailbox-example.com

2.) Dominic Updike
Property Investor
Mobile: +44(0)7700987654
Email: dominic.quillmarsh@mailbox-example.com

```html
<!DOCTYPE html>
<html lang="en">
<head>
<meta charset="utf-8">
<title>Quillmarsh Property Solutions – Business Card</title>
<link rel="stylesheet" href="https://fonts.googleapis.com/css2?family=Open+Sans:wght@400;600;700&display=swap">
<style>
  :root {
    --page-bg: #e8e8ee;
    --card-white: #ffffff;
    --card-green: #0f9a45;
    --card-green-light: #1eb25a;
    --brand-grey: #8a8a8a;
    --text-grey: #4a4a4a;
    --name-blue: #1a56c4;
    --rule-grey: #d2d2d2;
    --icon-blue: #2a6fd6;
  }
  * { box-sizing: border-box; margin: 0; padding: 0; }
  html, body {
    width: 1200px; height: 987px; overflow: hidden;
    background: var(--page-bg);
    font-family: "Open Sans", Arial, sans-serif;
  }
  .sheet {
    width: 1200px; height: 987px;
    display: flex; align-items: center; justify-content: center; gap: 60px;
  }
  .card {
    width: 520px; height: 300px;
    border-radius: 28px;
    position: relative;
    overflow: hidden;
    box-shadow: 0 6px 18px rgba(0,0,0,0.12);
  }
  /* Front */
  .card--front { background: var(--card-white); }
  .brand {
    position: absolute; top: 42px; left: 0; right: 0;
    display: flex; align-items: center; justify-content: center; gap: 12px;
  }
  .brand__square { width: 22px; height: 22px; background: var(--brand-grey); }
  .brand__name {
    font-weight: 700; font-size: 24px; letter-spacing: 1px;
    color: var(--brand-grey); text-transform: uppercase;
  }
  .brand__sub {
    position: absolute; top: 82px; left: 0; right: 0; text-align: center;
    font-weight: 700; font-size: 13px; letter-spacing: 2px;
    color: var(--brand-grey); text-transform: uppercase;
  }
  .rule {
    position: absolute; left: 36px; right: 36px; height: 2px;
    background: linear-gradient(90deg, transparent, var(--rule-grey) 15%, var(--rule-grey) 85%, transparent);
  }
  .rule--top { top: 120px; }
  .rule--bottom { top: 262px; }
  .contact { position: absolute; top: 138px; left: 48px; }
  .contact__person { font-size: 19px; color: var(--text-grey); margin-bottom: 12px; }
  .contact__name { color: var(--name-blue); font-weight: 600; }
  .contact__line {
    display: flex; align-items: center; gap: 10px;
    font-size: 15px; color: var(--text-grey); margin-bottom: 8px;
  }
  .contact__line svg { width: 14px; height: 14px; flex: none; }
  /* Back */
  .card--back {
    background: radial-gradient(circle at 55% 45%, var(--card-green-light), var(--card-green) 70%);
    display: flex; flex-direction: column; align-items: center; justify-content: center; gap: 18px;
  }
  .back-brand { display: flex; align-items: center; gap: 14px; }
  .back-brand__square { width: 30px; height: 30px; background: var(--card-white); }
  .back-brand__name {
    font-weight: 700; font-size: 32px; letter-spacing: 1px;
    color: var(--card-white); text-transform: uppercase;
  }
  .website { font-size: 18px; letter-spacing: 2px; color: var(--card-white); }
</style>
</head>
<body>
<main class="sheet">
  <section class="card card--front" aria-label="Card front">
    <div class="brand">
      <span class="brand__square"></span>
      <span class="brand__name">Quillmarsh</span>
    </div>
    <div class="brand__sub">Property Solutions</div>
    <div class="rule rule--top"></div>
    <div class="contact">
      <p class="contact__person"><span class="contact__name">Rosalind Updike,</span> Property Investor</p>
      <p class="contact__line">
        <svg viewBox="0 0 14 14" aria-hidden="true"><rect x="3.5" y="0.5" width="7" height="13" rx="1.5" fill="var(--icon-blue)"/><rect x="5" y="2.5" width="4" height="6" fill="#fff"/><circle cx="7" cy="11" r="1" fill="#fff"/></svg>
        +44(0)7700123456
      </p>
      <p class="contact__line">
        <svg viewBox="0 0 14 14" aria-hidden="true"><rect x="0.5" y="2.5" width="13" height="9" rx="1.5" fill="var(--icon-blue)"/><path d="M1.5 3.5 L7 8 L12.5 3.5" stroke="#fff" stroke-width="1.2" fill="none"/></svg>
        rosalind.quillmarsh@mailbox-example.com
      </p>
    </div>
    <div class="rule rule--bottom"></div>
  </section>

  <section class="card card--back" aria-label="Card back">
    <div class="back-brand">
      <span class="back-brand__square"></span>
      <span class="back-brand__name">Quillmarsh</span>
    </div>
    <p class="website">www.quillmarsh-example.com</p>
  </section>
</main>
</body>
</html>
```